New florist business website design

Number 1 want is an easy to navigate & check out website
Needs to be beautiful and eye catching as well.
This is an online only business (no shop front)
Rustic and blush pinks, neutrals, woods, leaves
Customers need to be able to go onto my website, select something they want to buy but have the option to use a drop down box to change colours of the flowers, or add notes to make changes to the arrangement

Industry/Entity Type

Florist

Coding

Coded - Design and coding required

Number of Pages Required

5+ page

Colors
f9d9e8
fff2ec
fffefc

Requirements
Must have
• Drop down menu to take you to other pages for Arrangements, bouquets, everlasting arrangements, gifts, contact
Be able to purchase and “add to basket”
Checkout page
Nice to have
• Be able to add my own photos once I’ve taken new ones
Should not have
• Tacky images or clip art

```html
<!DOCTYPE html>
<html lang="en">
<head>
<meta charset="utf-8">
<title>Fern &amp; Bloom — Online Florist</title>
<link href="https://fonts.googleapis.com/css2?family=Poppins:ital,wght@0,300;0,400;0,500;0,600;0,700;1,300;1,400;1,800&display=swap" rel="stylesheet">
<style>
:root{
  --peach:#fde3d6;
  --peach-light:#ffeee6;
  --blush:#f6cfe3;
  --cream:#fffefc;
  --sand:#fbe3c8;
  --ink:#1d1d1f;
  --muted:#4a4a4a;
  --accent:#d2378a;
  --line:#e7c9c0;
  --leaf:#5f7a3c;
  --wood:#8a5a3c;
}
*{box-sizing:border-box;margin:0;padding:0}
html,body{width:1200px;height:4431px;overflow:hidden}
body{font-family:'Poppins',sans-serif;color:var(--ink);position:relative;
  background:linear-gradient(180deg,var(--peach) 0%,var(--peach-light) 25%,var(--peach) 50%,var(--peach-light) 75%,var(--peach) 100%)}
.abs{position:absolute}
/* header */
.site-header{left:0;top:0;width:1200px;height:150px;background:var(--peach)}
.nav a{position:absolute;top:63px;font-size:17px;color:var(--ink);text-decoration:none;white-space:nowrap}
.brand{left:515px;top:55px;width:170px;height:36px;display:flex;align-items:center;justify-content:center;gap:8px;font-size:22px;font-weight:400;white-space:nowrap;color:var(--ink)}
.brand-dot{width:10px;height:10px;border-radius:50%;background:var(--accent);flex:none}
.cart-count{font-size:12px;color:var(--accent)}
/* hero */
.hero{left:0;top:146px;width:1200px;height:700px;
  background:
    linear-gradient(180deg,rgba(40,25,15,.15),rgba(40,25,15,.35)),
    radial-gradient(ellipse 260px 330px at 590px 300px,#e9b79a 0%,#c98e6e 45%,transparent 70%),
    radial-gradient(ellipse 300px 260px at 980px 380px,#d9593c 0%,#7c8b3a 55%,transparent 80%),
    radial-gradient(ellipse 260px 260px at 140px 520px,#a3273a 0%,#4a5d2c 60%,transparent 85%),
    linear-gradient(100deg,#3d3a2a 0%,#6c5a3e 30%,#8b6a4e 50%,#5e6c35 75%,#3a3d28 100%)}
.hero-title{left:0;width:1200px;text-align:center;color:#fff;font-weight:800;font-style:italic;white-space:nowrap;text-shadow:0 2px 10px rgba(0,0,0,.35)}
.btn{display:flex;align-items:center;justify-content:center;background:var(--sand);color:var(--ink);font-size:19px}
.edge{left:0;width:1200px;height:34px}
/* featured */
.section-title{left:0;width:1200px;text-align:center;font-size:36px;font-weight:500}
.card{width:242px;height:374px;text-align:center}
.card.active{background:var(--cream);box-shadow:0 2px 14px rgba(0,0,0,.13)}
.card-img{position:absolute;left:0;top:0;width:242px;height:217px}
.card-name{position:absolute;top:240px;width:100%;font-size:17px;font-weight:500}
.card-cat{position:absolute;top:267px;width:100%;font-size:14px;color:var(--muted)}
.card-price{position:absolute;top:297px;width:100%;font-size:34px;font-weight:300}
.card-price sup{font-size:17px}
.card-btn{position:absolute;left:60px;top:352px;width:122px;height:40px;background:#f7cde0;font-size:15px;font-weight:500;display:flex;align-items:center;justify-content:center}
/* bands */
.band{left:0;width:1200px;background:var(--blush)}
.h2{font-size:36px;font-weight:500;line-height:1.15}
.body-text{font-size:17px;line-height:35px;color:var(--muted)}
.round-photo{border-radius:50%}
.ring{border:1.5px solid #333;border-radius:50%}
/* ranges */
.tile{overflow:hidden}
.tile-name{position:absolute;font-size:50px;font-style:italic;font-weight:300;color:var(--ink);line-height:1}
.tile-sub{position:absolute;font-size:17px;color:var(--ink);white-space:nowrap}
.tile.dark .tile-name,.tile.dark .tile-sub{color:#fff}
/* reviews */
.quote{left:100px;width:1000px;text-align:center;font-style:italic;font-size:19px;line-height:35px;color:var(--muted)}
.feature{width:512px;height:227px}
.feature-frame{position:absolute;left:10px;top:10px;right:10px;bottom:10px;border:2px solid #fff}
.feature-text{position:absolute;left:0;top:0;width:100%;height:100%;display:flex;align-items:center;justify-content:center;font-size:42px;font-style:italic;font-weight:300;color:#fff}
/* footer */
.footer-head{font-size:22px;font-weight:500;color:#333}
.footer-link{font-size:15px;color:#444}
.social{width:26px;height:26px;border-radius:50%;background:#2c2c2c}
</style>
</head>
<body>

<header class="abs site-header">
  <nav class="nav">
    <a style="left:75px">Home</a>
    <a style="left:165px">About Us</a>
    <a style="left:282px">Flowers ▾</a>
    <a style="left:402px">Services ▾</a>
    <a style="left:776px">Gifts</a>
    <a style="left:854px">Contact</a>
  </nav>
  <div class="abs brand"><span class="brand-dot"></span>Fern &amp; Bloom</div>
  <svg class="abs" style="left:1000px;top:62px" width="100" height="24" viewBox="0 0 100 24">
    <circle cx="9" cy="10" r="6" fill="none" stroke="#111" stroke-width="2.5"/><line x1="13" y1="14" x2="18" y2="19" stroke="#111" stroke-width="2.5"/>
    <circle cx="48" cy="7" r="5" fill="#111"/><path d="M39 20q9-10 18 0z" fill="#111"/>
    <path d="M78 9h18l-3 10h-12z" fill="#111"/><path d="M82 9l5-6 5 6" fill="none" stroke="#111" stroke-width="2"/>
  </svg>
  <span class="abs cart-count" style="left:1102px;top:58px">(0)</span>
</header>

<section class="abs hero" role="img" aria-label="Smiling florist holding fresh tulips in a flower-filled shop"></section>
<svg class="abs edge" style="top:134px" viewBox="0 0 1200 34" preserveAspectRatio="none"><path d="M0 0H1200V16l-40 6-50-9-60 12-70-7-50 10-80-8-60 9-70-10-60 8-70-7-50 11-80-9-60 7-70-10-60 9-70-7-50 10-70-9-60 7-40-6V0z" fill="var(--peach)"/></svg>
<svg class="abs edge" style="top:820px" viewBox="0 0 1200 34" preserveAspectRatio="none"><path d="M0 34H1200V12l-50 9-60-11-70 8-50-10-80 9-60-7 70 10-130-9-70 8-50-11-80 9-60-8-70 10-60-9-70 7-50-10-70 9-60-7-40 7z" fill="var(--peach)"/></svg>
<div class="abs hero-title" style="top:418px;font-size:74px">Welcome to Fern &amp; Bloom</div>
<div class="abs hero-title" style="top:505px;font-size:46px">Online Florist Business</div>
<div class="abs btn" style="left:511px;top:585px;width:179px;height:53px">Shop Now</div>

<h2 class="abs section-title" style="top:905px">Featured Flowers</h2>
<div class="abs card active" style="left:74px;top:976px">
  <div class="card-img" role="img" aria-label="Bouquet of red roses" style="background:radial-gradient(ellipse 70px 60px at 50% 40%,#b8142a,#d8505c 55%,transparent 80%),radial-gradient(ellipse 40px 60px at 50% 85%,#4d6b32,transparent 75%),var(--cream)"></div>
  <div class="card-name">Schefflera</div><div class="card-cat">Bouquets, House Plants</div>
  <div class="card-price"><sup>$</sup>16</div>
  <div class="card-btn">Add to Cart</div>
</div>
<div class="abs card" style="left:342px;top:976px">
  <div class="card-img" role="img" aria-label="Mixed bouquet of daisies and roses" style="background:radial-gradient(ellipse 80px 55px at 50% 42%,#f3ece2,#d83a6a 45%,#6a4aa0 65%,transparent 82%),radial-gradient(ellipse 35px 50px at 50% 85%,#4d7a32,transparent 75%),var(--cream)"></div>
  <div class="card-name">Schefflera</div><div class="card-cat">Bouquets, House Plants</div>
  <div class="card-price"><sup>$</sup>16</div>
</div>
<div class="abs card" style="left:614px;top:976px">
  <div class="card-img" role="img" aria-label="Purple tulips lying on their side" style="background:radial-gradient(ellipse 95px 35px at 50% 55%,#5a2a7a,#7a9a4a 60%,transparent 85%),var(--cream)"></div>
  <div class="card-name">Schefflera</div><div class="card-cat">Bouquets, House Plants</div>
  <div class="card-price"><sup>$</sup>16</div>
</div>
<div class="abs card" style="left:884px;top:976px">
  <div class="card-img" role="img" aria-label="Bunch of red tulips" style="background:radial-gradient(ellipse 45px 40px at 50% 32%,#e0243a,#ec7080 60%,transparent 85%),radial-gradient(ellipse 18px 55px at 50% 72%,#6a9a3a,transparent 80%),var(--cream)"></div>
  <div class="card-name">Schefflera</div><div class="card-cat">Bouquets, House Plants</div>
  <div class="card-price"><sup>$</sup>16</div>
</div>

<section class="abs band" style="top:1427px;height:507px"></section>
<svg class="abs edge" style="top:1410px" viewBox="0 0 1200 34" preserveAspectRatio="none"><path d="M0 34V16l60-8 70 10 60-9 80 8 50-10 70 9 60-7 70 10 60-8 80 9 50-11 70 8 60-7 70 10 60-9 80 8 50-10 70 9 40-6V34z" fill="var(--blush)"/></svg>
<svg class="abs edge" style="top:1918px" viewBox="0 0 1200 34" preserveAspectRatio="none"><path d="M0 0V16l50 9 70-10 60 8 80-9 50 11 70-8 60 7 70-10 60 9 80-8 50 10 70-9 60 7 70-10 60 8 80-9 50 10 70-8 40 6V0z" fill="var(--blush)"/></svg>
<h2 class="abs h2" style="left:74px;top:1550px">About Fern &amp; Bloom</h2>
<p class="abs body-text" style="left:74px;top:1610px;width:610px">Lorem ipsum proin gravida nibh vel velit auctor aliquean sol licitudinlorem quis bibendum auctor, nisi elit consequat ipsum, nec sagittis sem nibh id elit. Duis sed odio sit amet nibh vulputate cursus a sit amet mauris. Morbi accumsan ipsum velit.</p>
<div class="abs btn" style="left:74px;top:1777px;width:180px;height:54px">Read More</div>
<div class="abs ring" style="left:728px;top:1513px;width:360px;height:360px"></div>
<div class="abs round-photo" role="img" aria-label="Florist in apron arranging a bouquet" style="left:766px;top:1517px;width:344px;height:344px;background:radial-gradient(ellipse 90px 110px at 58% 35%,#f0d2bc,transparent 70%),radial-gradient(ellipse 80px 120px at 60% 75%,#3f5f9a,transparent 75%),linear-gradient(135deg,#b8243e 0%,#e07a8a 35%,#c9a07a 60%,#4a3a2e 100%)"></div>

<h2 class="abs section-title" style="top:1985px">Our Ranges</h2>
<div class="abs tile" style="left:74px;top:2068px;width:519px;height:461px;background:radial-gradient(ellipse 240px 170px at 35% 78%,#d52f78,#3f7a3a 60%,transparent 80%),linear-gradient(150deg,#f8d0dc,#f2b3c8 60%,#ea9ab8)" role="img" aria-label="Pink tulips on a pink background">
  <div class="tile-name" style="left:263px;top:78px">Tulips</div>
  <div class="tile-sub" style="left:263px;top:138px">Lorem ipsum proin gravida</div>
</div>
<div class="abs tile" style="left:609px;top:2068px;width:517px;height:225px;background:radial-gradient(ellipse 150px 70px at 78% 45%,#6a4ab8,#8a78c8 45%,#7a9a5a 65%,transparent 85%),#fff" role="img" aria-label="Sprigs of lavender">
  <div class="tile-name" style="left:22px;top:125px">Lavender</div>
  <div class="tile-sub" style="left:26px;top:178px">Lorem ipsum proin gravida</div>
</div>
<div class="abs tile dark" style="left:609px;top:2303px;width:252px;height:226px;background:radial-gradient(ellipse 90px 70px at 55% 35%,#ee8a6a,#c8503a 55%,transparent 85%),linear-gradient(135deg,#3a2a20,#6a4a38 50%,#2e2a1e)" role="img" aria-label="Coral roses">
  <div class="tile-name" style="left:22px;top:135px">Rose</div>
  <div class="tile-sub" style="left:26px;top:188px">Lorem ipsum proin</div>
</div>
<div class="abs tile dark" style="left:873px;top:2303px;width:253px;height:226px;background:radial-gradient(ellipse 100px 80px at 65% 55%,#f4f0ea,#d8d2c0 50%,transparent 80%),linear-gradient(135deg,#d0a848,#a08a5a 50%,#4a4a3a)" role="img" aria-label="White lilies">
  <div class="tile-name" style="left:22px;top:135px">Lilly</div>
  <div class="tile-sub" style="left:26px;top:188px">Lorem ipsum pro</div>
</div>

<section class="abs band" style="top:2621px;height:499px"></section>
<svg class="abs edge" style="top:2604px" viewBox="0 0 1200 34" preserveAspectRatio="none"><path d="M0 34V14l70 9 60-10 80 8 50-9 70 10 60-8 70 9 60-10 80 8 50-9 70 10 60-7 70 9 60-10 80 8 50-9 70 9 60-8 40 6V34z" fill="var(--blush)"/></svg>
<svg class="abs edge" style="top:3104px" viewBox="0 0 1200 34" preserveAspectRatio="none"><path d="M0 0V15l60 9 70-10 50 8 80-9 60 10 70-8 60 7 80-10 50 9 70-8 60 10 70-9 50 7 80-10 60 8 70-9 60 10 70-8 40 6V0z" fill="var(--blush)"/></svg>
<div class="abs ring" style="left:112px;top:2700px;width:360px;height:360px"></div>
<div class="abs round-photo" role="img" aria-label="Smiling florist arranging flowers in a glass vase" style="left:78px;top:2700px;width:352px;height:352px;background:radial-gradient(ellipse 80px 100px at 35% 40%,#e6c2a4,transparent 70%),radial-gradient(ellipse 110px 150px at 70% 45%,#c8d89a,transparent 75%),linear-gradient(135deg,#e8e4d8 0%,#a9b870 45%,#6a7a4a 75%,#3a4030 100%)"></div>
<h2 class="abs h2" style="left:524px;top:2710px">Whatever the occasion,<br>our flowers will make it special!</h2>
<p class="abs body-text" style="left:524px;top:2815px;width:610px">Lorem ipsum proin gravida nibh vel velit auctor aliquean sol licitudinlorem quis bibendum auctor, nisi elit consequat ipsum, nec sagittis sem nibh id elit. Duis sed odio sit amet nibh vulputate cursus a sit amet mauris. Morbi accumsan ipsum velit.</p>
<div class="abs btn" style="left:524px;top:2982px;width:181px;height:52px">Read More</div>

<h2 class="abs section-title" style="top:3172px">Customer Reviews</h2>
<svg class="abs" style="left:476px;top:3300px" width="250" height="30" viewBox="0 0 250 30"><path d="M18 3L6 15l12 12" fill="none" stroke="#333" stroke-width="2"/><path d="M232 3l12 12-12 12" fill="none" stroke="#333" stroke-width="2"/></svg>
<div class="abs round-photo" role="img" aria-label="Portrait of a smiling customer" style="left:522px;top:3238px;width:152px;height:152px;background:radial-gradient(ellipse 35px 45px at 50% 40%,#ecd0bc,transparent 75%),linear-gradient(180deg,#8a7aa8 0%,#d86a5a 60%,#b83a3a 100%)"></div>
<p class="abs quote" style="top:3409px">“ Duis sed odio sit amet nibh vulputate cursus a sit amet mauris. Morbi accumsan ipsum velit. Lorem ipsum proin gravida nibh vel velit auctor aliquean sollicitudinlorem quis bibendum auctor, nisi elit consequat ipsum, nec sagittis sem nibh id elit.”</p>
<div class="abs" style="left:0;top:3527px;width:1200px;text-align:center;color:var(--accent);font-weight:600;font-size:17px">Maren Holloway</div>

<div class="abs feature" style="left:74px;top:3627px;background:radial-gradient(ellipse 160px 80px at 40% 35%,#4a2a3a,transparent 80%),linear-gradient(135deg,#2e2a22,#4a3a32 45%,#5a6a3a 80%,#2a3222)" role="img" aria-label="Dark tulips being hand picked into a basket">
  <div class="feature-frame"></div><div class="feature-text">Hand Picked</div>
</div>
<div class="abs feature" style="left:615px;top:3627px;width:511px;background:radial-gradient(ellipse 150px 110px at 50% 50%,#e0282e,#a01822 45%,transparent 75%),linear-gradient(135deg,#2e3a26,#4a5a34 50%,#262e20)" role="img" aria-label="Red dahlia in bloom">
  <div class="feature-frame"></div><div class="feature-text">Unique Flowers</div>
</div>

<footer>
  <div class="abs footer-head" style="left:74px;top:4036px">Company</div>
  <div class="abs footer-link" style="left:74px;top:4088px;line-height:44px">About<br>Contact<br>Blog<br>Terms of Service<br>Refund policy</div>
  <div class="abs footer-head" style="left:316px;top:4036px">Help</div>
  <div class="abs footer-link" style="left:316px;top:4088px;line-height:44px">Nam libero tempore<br>Cum soluta<br>Est eligendi optio<br>Cumque nihil<br>Impedit</div>
  <div class="abs footer-head" style="left:554px;top:4036px">Contact Us</div>
  <div class="abs footer-link" style="left:554px;top:4088px;line-height:37px">8:00am - 5:00pm CST<br>1-800-555-0142<br>hello@fernbloom.com</div>
  <div class="abs footer-head" style="left:834px;top:4036px">Email Sign Up</div>
  <div class="abs footer-link" style="left:834px;top:4082px;width:300px;line-height:26px">Nam libero tempore, cum soluta nobis est eligendi optio cumque nihil impedit</div>
  <div class="abs" style="left:832px;top:4161px;width:294px;height:47px;background:#f2ebe6;font-size:14px;color:#555;padding:14px 14px">Email Address</div>
  <div class="abs" style="left:832px;top:4218px;width:294px;height:48px;background:#f7c6dd;font-size:18px;display:flex;align-items:center;justify-content:center">Subscribe</div>
  <div class="abs" style="left:0;top:4340px;width:1200px;height:1px;background:var(--line)"></div>
  <div class="abs" style="left:74px;top:4372px;font-size:13px;color:#444">Copyright © 2021. CompanyName. All Right Reserved</div>
  <div class="abs" style="left:902px;top:4366px;display:flex;gap:24px" aria-label="Social links">
    <span class="social"></span><span class="social"></span><span class="social"></span><span class="social"></span><span class="social"></span>
  </div>
</footer>
</body>
</html>
```